Marlowe Group needs a business card

I would like the card to be simple but modern and elegant.
I like black and white.
or black and gold.
we are a private finance lender and also are involved in property and property developments.

please look at the business card photos i provided i would like M.G only one one side and all the other details on the other side use fonts that tie in with my theme.

Industry/Entity Type

Finance

Contact Information for Business Card

Marlowe Group (M.G) Daniel Marlowe M: 0413586207 E: danmarl@inboxmail.test

Font styles to use
Other font styles liked:
• Use fonts that would reflect our business

Colors
000000
ffffff

Requirements
Must have
• one side of details
• other side has either M.G or Marlowe Group like in the photos provided

```html
<!DOCTYPE html>
<html lang="en">
<head>
<meta charset="UTF-8">
<title>Marlowe Group – Business Card</title>
<link rel="stylesheet" href="https://fonts.googleapis.com/css2?family=Open+Sans:wght@400;600;800&display=swap">
<style>
  :root {
    --backdrop: #3b3532;
    --card-black: #000000;
    --card-white: #ffffff;
    --ink: #111111;
    --rule: #1a1a1a;
  }
  * { margin: 0; padding: 0; box-sizing: border-box; }
  html, body {
    width: 1200px;
    height: 827px;
    overflow: hidden;
  }
  body {
    background: var(--backdrop);
    font-family: "Open Sans", Arial, sans-serif;
    position: relative;
  }
  .card {
    position: absolute;
    top: 256px;
    width: 520px;
    height: 315px;
    border-radius: 3px;
    box-shadow: 0 10px 24px rgba(0, 0, 0, 0.45);
  }
  .card-back {
    left: 50px;
    background: var(--card-black);
  }
  .monogram {
    position: absolute;
    left: 185px;
    top: 78px;
    color: var(--card-white);
    font-size: 58px;
    font-weight: 400;
    letter-spacing: 1px;
  }
  .card-front {
    left: 630px;
    background: var(--card-white);
    color: var(--ink);
  }
  .brand {
    position: absolute;
    right: 60px;
    top: 58px;
    text-align: right;
  }
  .brand-name {
    font-size: 38px;
    font-weight: 800;
    letter-spacing: -1px;
    line-height: 1;
    color: var(--ink);
  }
  .brand-rule {
    height: 1.5px;
    width: 110px;
    margin-left: auto;
    margin-top: 8px;
    background: var(--rule);
  }
  .rule {
    position: absolute;
    left: 36px;
    right: 36px;
    height: 1.5px;
    background: var(--rule);
  }
  .rule-top { top: 140px; }
  .rule-bottom { top: 272px; }
  .holder-name {
    position: absolute;
    left: 196px;
    top: 152px;
    font-size: 24px;
    font-weight: 400;
  }
  .contact {
    position: absolute;
    display: flex;
    align-items: center;
    gap: 8px;
    font-size: 15px;
  }
  .contact svg { width: 16px; height: 16px; flex: none; }
  .contact-phone { left: 40px; top: 156px; }
  .contact-email { right: 40px; top: 222px; }
</style>
</head>
<body>
  <section class="card card-back" aria-label="Card back">
    <div class="monogram">M.G</div>
  </section>

  <section class="card card-front" aria-label="Card front">
    <div class="brand">
      <div class="brand-name">Marlowe Group</div>
      <div class="brand-rule"></div>
    </div>

    <div class="rule rule-top"></div>

    <div class="contact contact-phone">
      <svg viewBox="0 0 16 16" aria-hidden="true">
        <rect width="16" height="16" rx="3" fill="#111"/>
        <rect x="5" y="2.5" width="6" height="11" rx="1" fill="#fff"/>
        <rect x="6" y="4" width="4" height="5" fill="#111"/>
        <circle cx="8" cy="11.5" r="0.8" fill="#111"/>
      </svg>
      <span>0413586207</span>
    </div>

    <div class="holder-name">Daniel Marlowe</div>

    <div class="contact contact-email">
      <svg viewBox="0 0 16 16" aria-hidden="true">
        <rect width="16" height="16" rx="3" fill="#111"/>
        <rect x="3" y="4.5" width="10" height="7" fill="#fff"/>
        <path d="M3 4.5 L8 8.8 L13 4.5" fill="none" stroke="#111" stroke-width="1"/>
      </svg>
      <span>danmarl@inboxmail.test</span>
    </div>

    <div class="rule rule-bottom"></div>
  </section>
</body>
</html>
```